Need help in designing new business card utilizing our new logo.

BuildMark Solutions works with Construction Business Owners, Managers & IT Professionals to strengthen software usage and increase user productivity.

Our Construction Accounting and Mobile Field Management Software Clients engage with us in the following areas:

New Software Implementations
Software Re-Implementations
Redesigning Software Usage at the User Level
Project Coordination & Management
Continued Software Support

Old tag line:
Weighing Options - Implementing Solutions

www.buildmark-solutions.example

Ridge 4 is a product, but not needed for a new business card.

```html
<!DOCTYPE html>
<html lang="en">
<head>
<meta charset="utf-8">
<title>BuildMark Solutions — Business Card</title>
<link rel="stylesheet" href="https://fonts.googleapis.com/css2?family=Open+Sans:wght@400;600;700&family=Oswald:wght@400;500&display=swap">
<style>
  :root {
    --brand-blue: #0c15a3;
    --ink: #3a3a3a;
    --paper: #ffffff;
    --backdrop: #6a6a6a;
    --rule: #c9c9c9;
  }
  * { box-sizing: border-box; margin: 0; padding: 0; }
  html, body { width: 1200px; height: 802px; overflow: hidden; }
  body {
    background: var(--backdrop);
    font-family: "Open Sans", sans-serif;
    position: relative;
  }
  .card {
    position: absolute;
    top: 274px;
    width: 443px;
    height: 265px;
    background: var(--paper);
    overflow: hidden;
  }
  .card--front { left: 136px; }
  .card--back { left: 624px; }

  /* Front */
  .brand {
    position: absolute;
    left: 30px;
    top: 121px;
    display: flex;
    align-items: center;
    gap: 8px;
    white-space: nowrap;
  }
  .brand__mark {
    width: 13px; height: 13px;
    background: var(--brand-blue);
    flex: none;
  }
  .brand__name {
    font-size: 15px;
    font-weight: 700;
    color: var(--brand-blue);
    line-height: 18px;
  }
  .divider {
    position: absolute;
    left: 222px; top: 60px;
    width: 1px; height: 142px;
    background: var(--rule);
  }
  .contact {
    position: absolute;
    left: 236px; top: 61px;
    color: var(--ink);
    white-space: nowrap;
  }
  .contact__name {
    font-size: 16.5px;
    font-weight: 700;
    color: var(--brand-blue);
    line-height: 1.1;
  }
  .contact__role {
    font-size: 13px;
    margin-bottom: 7px;
  }
  .contact__list { list-style: none; font-size: 11.8px; line-height: 16px; }
  .contact__list li { display: flex; align-items: center; gap: 4px; }
  .contact__list svg { width: 9px; height: 9px; fill: var(--brand-blue); flex: none; }
  .contact__address { font-size: 12.4px; line-height: 16px; margin-top: 3px; }

  /* Back */
  .band {
    position: absolute;
    left: 0; top: 0;
    width: 158px; height: 100%;
    background: var(--brand-blue);
  }
  .tagline {
    position: absolute;
    left: -64px; top: 106px;
    width: 265px; height: 54px;
    transform: rotate(-90deg);
    font-family: "Oswald", sans-serif;
    font-weight: 500;
    font-size: 15px;
    line-height: 26px;
    color: var(--paper);
    text-transform: uppercase;
    text-align: center;
    white-space: nowrap;
  }
  .services { list-style: none; }
  .service {
    position: absolute;
    left: 129px;
    display: flex;
    align-items: center;
    gap: 9px;
    font-size: 10.4px;
    line-height: 13px;
    color: #222;
    text-transform: uppercase;
    white-space: nowrap;
  }
  .service__icon {
    width: 40px; height: 40px;
    border-radius: 50%;
    background: var(--paper);
    border: 2px solid var(--brand-blue);
    display: flex; align-items: center; justify-content: center;
    flex: none;
  }
  .service__icon svg { width: 24px; height: 24px; }
</style>
</head>
<body>

<section class="card card--front" aria-label="Business card front">
  <div class="brand">
    <span class="brand__mark"></span>
    <span class="brand__name">BuildMark Solutions</span>
  </div>
  <div class="divider"></div>
  <div class="contact">
    <p class="contact__name">DORIAN WELLS</p>
    <p class="contact__role">Managing Director</p>
    <ul class="contact__list">
      <li><svg viewBox="0 0 10 10"><path d="M1 3c0-1 1-2 4-2s4 1 4 2v1H7V3H3v1H1zM2 5h6l1 4H1z"/></svg>044-555 018 226</li>
      <li><svg viewBox="0 0 10 10"><path d="M2.5 0h5v10h-5zM3.5 1v7h3V1z"/></svg>044-555 018 226</li>
      <li><svg viewBox="0 0 10 10"><path d="M0 2h10v6H0zM1 3l4 3 4-3"/></svg>info@buildmark.example</li>
      <li><svg viewBox="0 0 10 10"><circle cx="5" cy="5" r="5"/></svg>www.buildmark-solutions.example</li>
    </ul>
    <p class="contact__address">48 Quarry Lane, Suite 3<br>Northvale, 204816.</p>
  </div>
</section>

<section class="card card--back" aria-label="Business card back">
  <div class="band"></div>
  <p class="tagline">Weighing Options<br>Implementing Solutions</p>
  <ul class="services">
    <li class="service" style="top:10px">
      <span class="service__icon"><svg viewBox="0 0 24 24" fill="#0c15a3"><circle cx="12" cy="7" r="4"/><path d="M5 19c0-4 3-7 7-7s7 3 7 7z"/><circle cx="3" cy="14" r="2"/><circle cx="21" cy="14" r="2"/></svg></span>
      Project Coordination &amp; Management
    </li>
    <li class="service" style="top:60px">
      <span class="service__icon"><svg viewBox="0 0 24 24" fill="none" stroke="#0c15a3" stroke-width="2.2"><circle cx="11" cy="13" r="7"/><circle cx="11" cy="13" r="1.5" fill="#0c15a3"/><path d="M18 3v6M15 6h6"/></svg></span>
      New Software Implementations
    </li>
    <li class="service" style="top:109px">
      <span class="service__icon"><svg viewBox="0 0 24 24" fill="none" stroke="#0c15a3" stroke-width="2.2"><circle cx="12" cy="12" r="5"/><path d="M12 2v4M12 18v4M2 12h4M18 12h4"/></svg></span>
      Redesigning Software<br>Usage at the User Level
    </li>
    <li class="service" style="top:160px">
      <span class="service__icon"><svg viewBox="0 0 24 24" fill="none" stroke="#0c15a3" stroke-width="2.2"><circle cx="11" cy="13" r="7"/><circle cx="11" cy="13" r="1.5" fill="#0c15a3"/><path d="M16 3a5 5 0 0 1 5 5M21 4v4h-4"/></svg></span>
      Software Re-Implementations
    </li>
    <li class="service" style="top:209px">
      <span class="service__icon"><svg viewBox="0 0 24 24" fill="#0c15a3"><circle cx="12" cy="8" r="4"/><path d="M5 21c0-4 3-7 7-7s7 3 7 7z"/><path d="M4 9a8 8 0 0 1 16 0" fill="none" stroke="#0c15a3" stroke-width="2"/></svg></span>
      Continued Software Support
    </li>
  </ul>
</section>

</body>
</html>
```